Stickers Set for Archery brand

design a set of stickers of our name , logo and slogan
1. Round stickers
2. Rectangular stickers
3. Narrow (stick) stickers - 3/4inch x 6inch
4. window stickers
files attached show 2 versions of the logo, skull to be used, other designs we have for reference.

Target Market(s)

archery comunity

Colors

Designer to choose colors to be used in the design.

```html
<!DOCTYPE html>
<html lang="en">
<head>
<meta charset="utf-8">
<title>Northwind Bows – Narrow Sticker</title>
<link rel="stylesheet" href="https://fonts.googleapis.com/css2?family=Montserrat:wght@500&display=swap">
<style>
  :root {
    --sticker-gold: #ae954c;
    --ink-black: #000000;
  }
  html, body {
    margin: 0;
    padding: 0;
    overflow: hidden;
    background: var(--sticker-gold);
  }
  .sticker {
    position: relative;
    width: 1200px;
    height: 150px;
    background: var(--sticker-gold);
    overflow: hidden;
  }
  .sticker__art {
    position: absolute;
    inset: 0;
    width: 1200px;
    height: 150px;
  }
  .brand-mark__name,
  .slogan {
    font-family: "Montserrat", "Helvetica Neue", Arial, sans-serif;
    font-weight: 500;
    fill: var(--ink-black);
  }
  .brand-mark__name {
    font-size: 10px;
    letter-spacing: 0.3px;
  }
  .brand-mark__dot {
    fill: var(--ink-black);
  }
  .slogan {
    font-size: 111px;
  }
</style>
</head>
<body>
  <div class="sticker">
    <svg class="sticker__art" viewBox="0 0 1200 150" xmlns="http://www.w3.org/2000/svg">
      <g class="brand-mark" aria-label="Northwind Bows">
        <circle class="brand-mark__dot" cx="46" cy="64" r="32"/>
        <text class="brand-mark__name" x="46" y="124" text-anchor="middle">NORTHWIND</text>
      </g>
      <text class="slogan" x="161" y="115" textLength="989" lengthAdjust="spacingAndGlyphs">NORTHWIND BOWS</text>
    </svg>
  </div>
</body>
</html>
```